Clear Plastic Card Design

I am looking to have a business card designed from my logo icon. I am looking to match the style of a different business card I have attached in the files.
Looking for a card that is plastic, with layers of transparency in the shape of my logo icon (also attached in the files) - not a circle like the other card. The winning design will incorporate the red icon logo on the front and back and include the charity's name, "Light for the Weary Souls" in the same or similar font, as well as an email and phone number. For now, use the email: email@lightfortheweary-mail.org and the phone number 555-382-7194.
We like how the sample business card has transparency, partial and full opacity layers and a matching color scheme. Files will need to be in vector so that our business card printing company can work with it.
UPDATE:
We've some excellent designs in, thank you everyone! I got an early review from the owner, and he requested a minor redirect to find his perfect design. He wants the design to stand out by NOT being a rectangle. Try instead a circle, square, or best yet - something that falls in the outline of the logo icon, either fully or partially. Thank you, everyone!
Light for the Weary Souls text should be incorporated as well as a phone and email.

```html
<!DOCTYPE html>
<html lang="en">
<head>
<meta charset="UTF-8">
<title>Light for the Weary Souls — Round Card</title>
<link rel="stylesheet" href="https://fonts.googleapis.com/css2?family=Roboto:wght@400&display=swap">
<style>
  :root {
    --page-bg: #e4e4e4;
    --ember-orange: #f06a14;
    --flame-red: #e02a18;
    --crimson: #d81c44;
    --deep-red: #c4101c;
    --paper-white: #ffffff;
    --ink-grey: #333333;
    --band-ink: #3a3a3a;
  }
  html, body {
    margin: 0;
    padding: 0;
    width: 1175px;
    height: 1200px;
    overflow: hidden;
    background: var(--page-bg);
    font-family: "Roboto", Arial, sans-serif;
  }
  .round-card {
    position: absolute;
    left: 87px;
    top: 100px;
    width: 1000px;
    height: 1000px;
    border-radius: 50%;
    overflow: hidden;
  }
  .facet-backdrop {
    position: absolute;
    inset: 0;
    background:
      radial-gradient(circle at 80% 15%, var(--ember-orange) 0%, rgba(240,106,20,0) 55%),
      radial-gradient(circle at 15% 55%, var(--crimson) 0%, rgba(216,28,68,0) 50%),
      linear-gradient(160deg, var(--ember-orange) 0%, var(--flame-red) 45%, var(--deep-red) 75%, var(--crimson) 100%);
  }
  .brand-disc {
    position: absolute;
    left: 249px;
    top: 72px;
    width: 502px;
    height: 502px;
    border-radius: 50%;
    background: var(--paper-white);
    display: flex;
    flex-direction: column;
    align-items: center;
    justify-content: center;
  }
  .brand-dot {
    width: 120px;
    height: 120px;
    border-radius: 50%;
    background: var(--flame-red);
    margin-bottom: 34px;
  }
  .brand-name {
    margin: 0;
    font-weight: 400;
    font-size: 46px;
    line-height: 1.15;
    color: var(--ink-grey);
    text-align: center;
  }
  .contact {
    position: absolute;
    left: 0;
    width: 100%;
    margin: 0;
    text-align: center;
    color: var(--paper-white);
    font-size: 40px;
    line-height: 1;
  }
  .contact-phone { top: 614px; }
  .contact-email { top: 672px; }
  .web-band {
    position: absolute;
    left: 0;
    top: 744px;
    width: 100%;
    height: 83px;
    background: var(--paper-white);
    display: flex;
    align-items: center;
    justify-content: center;
    color: var(--band-ink);
    font-size: 41px;
  }
</style>
</head>
<body>
  <div class="round-card">
    <div class="facet-backdrop" role="img" aria-label="Faceted geometric background in orange, red and crimson tones"></div>
    <div class="brand-disc">
      <div class="brand-dot"></div>
      <p class="brand-name">Light for the<br>Weary Souls</p>
    </div>
    <p class="contact contact-phone">555-382-7194</p>
    <p class="contact contact-email">email@lightfortheweary-mail.org</p>
    <div class="web-band">www.lightforthewearysouls.org</div>
  </div>
</body>
</html>
```